New Company Business Card design

Looking for a corporate looking business card utilising my new logo design - the logo i would like embossed as one option and flat as another - simplistic but stylish - less is more - we are an import export business launching into the market - i would like a couple of options as main background - Grey or Black

```html
<!DOCTYPE html>
<html lang="en">
<head>
<meta charset="utf-8">
<title>Meridian Trade Partners – Business Card</title>
<link rel="stylesheet" href="https://fonts.googleapis.com/css2?family=Montserrat:wght@400;500;600&display=swap">
<style>
  :root {
    --stage: #3b3b3d;
    --card: #1e1e20;
    --card-deep: #19191b;
    --emboss: #2c2c2f;
    --emboss-light: #3a3a3e;
    --blue: #2a86d1;
    --white: #f2f2f2;
    --muted: #d9d9d9;
    --rule: #8a8a8a;
  }
  * { margin: 0; padding: 0; box-sizing: border-box; }
  html, body {
    width: 1200px; height: 900px; overflow: hidden;
    background: var(--stage);
    font-family: "Montserrat", Arial, sans-serif;
  }
  .stage {
    width: 1200px; height: 900px;
    display: flex; flex-direction: column; align-items: center; justify-content: center;
    gap: 36px;
  }
  .card {
    position: relative;
    width: 700px; height: 400px;
    background: var(--card);
    box-shadow: 0 14px 30px rgba(0,0,0,0.45);
    overflow: hidden;
  }
  /* Front: embossed wordmark */
  .card--front {
    display: flex; align-items: center; justify-content: center;
    background: var(--card-deep);
  }
  .brand {
    display: flex; align-items: center; gap: 16px;
  }
  .brand__dot {
    width: 22px; height: 22px; border-radius: 50%;
  }
  .brand__name {
    font-weight: 600; letter-spacing: 0.06em; text-transform: uppercase;
  }
  .card--front .brand__dot { background: var(--emboss-light); }
  .card--front .brand__name {
    font-size: 30px; color: var(--emboss-light);
  }
  /* Back: flat logo + contact */
  .card--back { display: flex; align-items: center; }
  .card--back .brand {
    width: 340px; justify-content: center; padding-left: 20px;
  }
  .card--back .brand__dot { background: var(--blue); width: 16px; height: 16px; }
  .card--back .brand__name {
    font-size: 19px; color: var(--blue); line-height: 1.25;
  }
  .divider {
    width: 1px; height: 200px; background: var(--rule);
  }
  .contact { padding-left: 40px; color: var(--white); }
  .contact__name { font-size: 23px; font-weight: 600; color: var(--blue); }
  .contact__role { font-size: 15px; color: var(--muted); margin-top: 4px; }
  .contact__address { font-size: 16px; line-height: 1.4; margin-top: 18px; }
  .contact__list { list-style: none; margin-top: 16px; font-size: 16px; }
  .contact__list li { display: flex; align-items: center; gap: 14px; line-height: 1.6; }
  .contact__list svg { width: 16px; height: 16px; flex: none; }
  .accent-band {
    position: absolute; left: 0; right: 0; bottom: 0; height: 10px;
    background: var(--blue);
  }
</style>
</head>
<body>
<main class="stage">
  <section class="card card--front" aria-label="Card front">
    <div class="brand">
      <span class="brand__dot"></span>
      <span class="brand__name">Meridian Trade Partners</span>
    </div>
  </section>

  <section class="card card--back" aria-label="Card back">
    <div class="brand">
      <span class="brand__dot"></span>
      <span class="brand__name">Meridian Trade<br>Partners</span>
    </div>
    <div class="divider"></div>
    <div class="contact">
      <p class="contact__name">Daniel Whitford</p>
      <p class="contact__role">Teaching Pastor</p>
      <p class="contact__address">418 N Willow Avenue<br>Clinton, MS 39056</p>
      <ul class="contact__list">
        <li>
          <svg viewBox="0 0 16 16" aria-hidden="true"><path d="M4 1.5l2.2 3-1.3 1.5c.8 1.8 2.3 3.3 4.1 4.1l1.5-1.3 3 2.2-1.2 2.5C7 13.5 2.5 9 1.5 2.7z" fill="none" stroke="var(--blue)" stroke-width="1.4" stroke-linejoin="round"/></svg>
          6015550148
        </li>
        <li>
          <svg viewBox="0 0 16 16" aria-hidden="true"><rect x="1.5" y="3.5" width="13" height="9" fill="none" stroke="var(--blue)" stroke-width="1.4"/><path d="M1.5 3.5L8 9l6.5-5.5" fill="none" stroke="var(--blue)" stroke-width="1.4"/></svg>
          daniel@yourwebsite.com
        </li>
        <li>
          <svg viewBox="0 0 16 16" aria-hidden="true"><circle cx="8" cy="8" r="6.5" fill="none" stroke="var(--blue)" stroke-width="1.4"/><ellipse cx="8" cy="8" rx="2.8" ry="6.5" fill="none" stroke="var(--blue)" stroke-width="1.2"/><path d="M1.5 8h13M2.5 5h11M2.5 11h11" stroke="var(--blue)" stroke-width="1.1"/></svg>
          www.yourwebsite.com
        </li>
      </ul>
    </div>
    <div class="accent-band"></div>
  </section>
</main>
</body>
</html>
```